Hardcore nerd needs to stand out in a sea of dull Defence business cards

Wombarra Devices is a new Australian consulting engineering company that turns research and theory into practical systems. No evangelistic fluff, just mathematics and physics into electronic and optical circuits for consumer products, scientific research or Defence applications.

We already have a recognised logo (provided) which is often dark blue/black on a light background but we're open to other combinations. (Us engineers tend to have limited aesthetic imagination :)

Some of our recent products have included:
* Instrumentation for electrical testing,
* Radar jammers,
* GPS antenna design,
* Satellite tracking systems,
* High power lasers

We're open to both single and double-sided designs - happy to be convinced either way.

P.S. Another group is working on the web page, so - alas - our web site is currently of no use for images/ideas...

Target Market(s)

Engineering managers,
Scientists

Contact Information for Business Card

Dr Colin Harte
R&D Engineer

colin@wombarradevices.com.au
0427 563 710

PO Box XXX (to be confirmed)
Kelsby ACT 2917
Australia

Font styles to use
Serif
Sans Serif

Colors

Designer to choose colors to be used in the design.

Requirements
Must have
• My contact details!
• I've had many (great) "bold and plain" designs submitted already, so feel free to be artistically creative :)
• Happy to take advice re fonts/colours/printability etc.
Nice to have
• I'm not sure if "lists" are more at home on a CV than a business card, but representative services include:
• Applied electromagnetics
• RF and high speed electronics
• Signal and image processing
• Electro-optical and laser systems
• Concept-to-prototype design services
• If you're considering double sided cards, then often measuring/alignment grids/rulers feature on the back of similar cards.
• e.g. https://www.veltranoptics.example/newgrouppage9.cfm?objectgroup_id=4183
• https://www.veltranoptics.example/newgrouppage9.cfm?objectgroup_ID=4185
• ..or even a "Smith chart" (google will return lots)
• Generic images to represent a capability might work - googling images associated with keyword for each of these areas might help:
• - "passive radar", "phased array", "fdtd", "vircator"
• RF and high speed electronic design
• - "smith chart", "microstrip circuits", "dimensioned drawing", "electronic schematic"
• - "dft", "iir filter"
• - "optical cavity". "laser energy level diagram"
• Background/watermarked images outlines/wireframes/schematics would probably look OK.
Should not have
• If a list of projects/services is provided, it is important not to make the client feel that this is "all" the company can do. Engineering design is a creative discipline (like graphics :)
• Please, no stock "military" snaps like planes, missiles, etc!

```html
<!DOCTYPE html>
<html lang="en">
<head>
<meta charset="utf-8">
<title>Wombarra Devices – Business Card</title>
<link rel="stylesheet" href="https://fonts.googleapis.com/css2?family=Montserrat:wght@400;600;700&display=swap">
<style>
  :root {
    --backdrop: #2f2a26;
    --card: #1d1e21;
    --ink: #f4f4f2;
    --ink-soft: #d9d9d6;
    --rule: #cfcfcc;
  }
  * { box-sizing: border-box; margin: 0; padding: 0; }
  html, body {
    width: 1200px; height: 716px; overflow: hidden;
    background: var(--backdrop);
    font-family: "Montserrat", sans-serif;
    color: var(--ink);
  }
  .canvas { position: relative; width: 1200px; height: 716px; }
  .card {
    position: absolute; width: 520px; height: 297px;
    background: var(--card);
    border-radius: 3px;
    box-shadow: 0 14px 30px rgba(0,0,0,.45);
  }
  .card--front { left: 60px; top: 120px; }
  .card--back  { left: 620px; top: 300px; }

  .brand { display: flex; align-items: center; gap: 12px; }
  .brand__dot {
    flex: none; border-radius: 50%;
    border: 7px solid var(--ink);
  }
  .brand__name {
    font-weight: 700; text-transform: uppercase; line-height: 1.05;
    color: var(--ink);
  }
  .brand__name span { display: block; }

  .card--front .brand {
    position: absolute; left: 50%; top: 50%;
    transform: translate(-50%, -50%);
  }
  .card--front .brand__dot { width: 70px; height: 70px; }
  .card--front .brand__name { font-size: 30px; letter-spacing: .5px; }
  .card--front .brand__name span + span { font-size: 17px; letter-spacing: 5px; }

  .card--back .brand { position: absolute; left: 40px; top: 108px; }
  .card--back .brand__dot { width: 50px; height: 50px; border-width: 5px; }
  .card--back .brand__name { font-size: 21px; }
  .card--back .brand__name span + span { font-size: 12px; letter-spacing: 3.5px; }

  .divider {
    position: absolute; left: 262px; top: 88px;
    width: 1px; height: 130px; background: var(--rule);
  }
  .contact { position: absolute; left: 282px; top: 96px; }
  .contact__name { font-weight: 700; font-size: 17px; letter-spacing: .6px; text-transform: uppercase; }
  .contact__role { font-size: 11px; color: var(--ink-soft); margin-top: 2px; }
  .contact__address { font-size: 11px; color: var(--ink-soft); margin-top: 12px; line-height: 1.35; }
  .contact__lines { list-style: none; margin-top: 10px; font-size: 11px; color: var(--ink-soft); line-height: 1.5; }
  .contact__lines li { display: flex; align-items: center; gap: 6px; }
  .contact__lines svg { width: 10px; height: 10px; fill: var(--ink-soft); flex: none; }
</style>
</head>
<body>
<main class="canvas">
  <section class="card card--front" aria-label="Card front">
    <div class="brand">
      <span class="brand__dot" aria-hidden="true"></span>
      <p class="brand__name"><span>Wombarra</span><span>Devices</span></p>
    </div>
  </section>

  <section class="card card--back" aria-label="Card back">
    <div class="brand">
      <span class="brand__dot" aria-hidden="true"></span>
      <p class="brand__name"><span>Wombarra</span><span>Devices</span></p>
    </div>
    <div class="divider"></div>
    <div class="contact">
      <h1 class="contact__name">Dr Colin Harte</h1>
      <p class="contact__role">R&amp;D Engineer</p>
      <p class="contact__address">PO Box XXX<br>Kelsby ACT 2917, Australia</p>
      <ul class="contact__lines">
        <li>
          <svg viewBox="0 0 10 10" aria-hidden="true"><path d="M2 0.5 L3.6 0.5 L4.2 3 L3 3.8 Q4 6 6.2 7 L7 5.8 L9.5 6.4 L9.5 8 Q9.5 9.5 8 9.5 Q0.5 9 0.5 2 Q0.5 0.5 2 0.5Z"/></svg>
          0427 563 710
        </li>
        <li>
          <svg viewBox="0 0 10 10" aria-hidden="true"><path d="M0.5 2 H9.5 V8 H0.5Z M1 2.5 L5 5.5 L9 2.5" fill="none" stroke="#d9d9d6" stroke-width="1"/></svg>
          colin@wombarradevices.com.au
        </li>
      </ul>
    </div>
  </section>
</main>
</body>
</html>
```